Clendora Hand Sanitizer One Page Website

I need someone to make a one page website for us. The site is www.clendora-example.com. I quickly created a simple basic page with all the elements (text, picture, table of pricing, pdf links) needed. I need someone to make the webpage look nice, professioonal, and responsive. There are only 2 links on the page pointing to two pdf files, otherwise there is no navigation needed. The product is a hand sanitizer.
Target Market(s)
Government, corporations, hospitals, large companies
Number of Pages Required
1 page
Requirements
Nice to have
- A hero image relating to hand sanitizer products would be really nice
We would like the bulleted items (Active Ingredient 75% Isopropyl Alcohol, etc) to somehow incorporate icons like the attached picture.

```html
<!DOCTYPE html>
<html lang="en">
<head>
<meta charset="utf-8">
<title>Clendora Hand Sanitizer</title>
<link href="https://fonts.googleapis.com/css2?family=Montserrat:wght@400;500;600;700;800&display=swap" rel="stylesheet">
<style>
  :root{
    --brand-blue:#1f66c8;
    --cyan:#29b9e3;
    --cyan-light:#8fe0f4;
    --navy:#1b2a3d;
    --navy-deep:#0a1d38;
    --footer-blue:#2d4d9c;
    --ink:#2b2f36;
    --muted:#6b7380;
    --white:#ffffff;
    --line:#e3e7ed;
    --btn-dark:#2a2e35;
  }
  *{box-sizing:border-box;margin:0;padding:0}
  html,body{width:824px;height:1200px;overflow:hidden}
  body{font-family:'Montserrat',sans-serif;color:var(--ink);background:var(--white);position:relative}

  .brand{font-weight:700;font-size:18px;letter-spacing:.5px;color:var(--navy);white-space:nowrap}

  .site-header{height:75px;display:flex;align-items:center;justify-content:space-between;padding:0 95px}
  .header-actions{display:flex;gap:6px}
  .btn{display:inline-block;font-size:7px;font-weight:700;letter-spacing:.5px;padding:8px 12px;text-transform:uppercase;color:var(--white)}
  .btn-blue{background:var(--cyan)}
  .btn-dark{background:var(--btn-dark)}
  .header-phone{display:flex;align-items:center;gap:8px}
  .header-phone small{display:block;font-size:7px;color:var(--muted)}
  .header-phone strong{font-size:18px;font-weight:700;color:var(--navy)}

  .hero{height:180px;background:linear-gradient(100deg,var(--cyan-light) 0%,var(--cyan) 60%,#1aa3d4 100%);position:relative;overflow:hidden}
  .hero-bottle{position:absolute;left:150px;top:16px;width:150px;height:164px;border-radius:22px 22px 0 0;background:linear-gradient(180deg,#e9f4f8,#bcd7e2)}
  .hero-copy{position:absolute;left:330px;top:40px}
  .ribbon-main{display:inline-block;background:var(--brand-blue);color:var(--white);font-size:17px;font-weight:600;padding:9px 36px 9px 22px;clip-path:polygon(0 0,100% 0,94% 100%,0 100%)}
  .ribbon-sub{display:block;margin-top:6px;width:300px;background:var(--navy);color:var(--white);font-size:16px;font-weight:700;padding:8px 22px;letter-spacing:.3px}
  .hero-cta{display:inline-block;margin-top:14px;background:var(--white);color:var(--navy);font-size:8px;font-weight:700;padding:9px 16px;letter-spacing:.5px}

  .product{height:315px;position:relative;padding:32px 95px}
  .product .brand{font-size:24px}
  .product-title{font-size:15px;font-weight:800;color:var(--navy);margin-top:6px;letter-spacing:.5px}
  .features{list-style:none;margin-top:18px;width:340px}
  .features li{display:flex;align-items:flex-start;gap:10px;font-size:9px;line-height:1.4;color:var(--muted);margin-bottom:10px}
  .features svg{flex:none}
  .product-photo{position:absolute;left:470px;top:45px;width:200px;height:200px;border-radius:50%;background:radial-gradient(circle,#f4f8fa 55%,#dfe8ee 100%);box-shadow:0 6px 20px rgba(0,0,0,.12);border:8px solid #f7f9fb}

  .pricing{height:255px;background:radial-gradient(ellipse at 50% 0%,#16406e 0%,var(--navy-deep) 70%);padding:45px 95px}
  .price-table{width:100%;border-collapse:collapse;background:var(--white);font-size:8px;text-align:center}
  .price-table th{background:var(--cyan);color:var(--white);font-weight:700;padding:12px 6px}
  .price-table td{padding:11px 6px;border-bottom:1px solid var(--line);color:var(--ink)}

  .site-footer{height:375px;background:linear-gradient(160deg,#3558aa,var(--footer-blue) 60%,#24418a);text-align:center;color:var(--white);padding-top:42px}
  .site-footer .brand{color:var(--white);font-size:22px}
  .stock-line{font-size:16px;font-weight:700;margin-top:22px}
  .call-line{font-size:22px;font-weight:800;color:var(--cyan-light);margin-top:8px}
  .footer-actions{display:flex;gap:8px;justify-content:center;margin-top:22px}
  .social{display:flex;gap:10px;justify-content:center;margin-top:22px}
  .social span{width:20px;height:20px;border-radius:50%;background:var(--white)}
  .copyright{font-size:7px;margin-top:20px;opacity:.85}
</style>
</head>
<body>
  <header class="site-header">
    <div class="brand">Halden Supply</div>
    <nav class="header-actions">
      <span class="btn btn-blue">Safety Data Sheet</span>
      <span class="btn btn-dark">Spec Sheet PDF</span>
    </nav>
    <div class="header-phone">
      <svg width="22" height="22" viewBox="0 0 24 24"><circle cx="12" cy="12" r="12" fill="#1f66c8"/><path d="M8.5 6.5l2 .2 1 3-1.4 1a7 7 0 003.2 3.2l1-1.4 3 1 .2 2c-.3.9-1.2 1.5-2 1.4A10 10 0 017 8.5c-.1-.8.5-1.7 1.5-2z" fill="#fff"/></svg>
      <div><small>Call us now</small><strong>555-014-2290</strong></div>
    </div>
  </header>

  <section class="hero">
    <div class="hero-bottle" role="img" aria-label="Gallon jug of Clendora hand sanitizer"></div>
    <div class="hero-copy">
      <span class="ribbon-main">Isopropyl Alcohol Antiseptic 75%</span>
      <span class="ribbon-sub">CLENDORA HAND SANITIZER</span>
      <span class="hero-cta">CONTACT US</span>
    </div>
  </section>

  <section class="product">
    <div class="brand">Halden Supply</div>
    <h2 class="product-title">HAND SANITIZER</h2>
    <ul class="features">
      <li><svg width="14" height="14" viewBox="0 0 14 14"><circle cx="7" cy="7" r="7" fill="#29b9e3"/><path d="M4 7.2l2 2 4-4" stroke="#fff" stroke-width="1.5" fill="none"/></svg>Active Ingredient 75% Isopropyl Alcohol</li>
      <li><svg width="14" height="14" viewBox="0 0 14 14"><circle cx="7" cy="7" r="7" fill="#29b9e3"/><path d="M4 7.2l2 2 4-4" stroke="#fff" stroke-width="1.5" fill="none"/></svg>FDA listed hand sanitizer, drug listing number 00000-000-01</li>
      <li><svg width="14" height="14" viewBox="0 0 14 14"><circle cx="7" cy="7" r="7" fill="#29b9e3"/><path d="M4 7.2l2 2 4-4" stroke="#fff" stroke-width="1.5" fill="none"/></svg>Meets World Health Organization (WHO) guidelines for an effective hand sanitizer</li>
      <li><svg width="14" height="14" viewBox="0 0 14 14"><circle cx="7" cy="7" r="7" fill="#29b9e3"/><path d="M4 7.2l2 2 4-4" stroke="#fff" stroke-width="1.5" fill="none"/></svg>Available in 1 &amp; 5 gallon and 275 gallon packages</li>
      <li><svg width="14" height="14" viewBox="0 0 14 14"><circle cx="7" cy="7" r="7" fill="#29b9e3"/><path d="M4 7.2l2 2 4-4" stroke="#fff" stroke-width="1.5" fill="none"/></svg>Effective in killing germs without drying out your hands</li>
    </ul>
    <div class="product-photo" role="img" aria-label="Gallon jug of Clendora hand sanitizer in a circular frame"></div>
  </section>

  <section class="pricing">
    <table class="price-table">
      <thead>
        <tr><th>Container</th><th>Min Order Qty</th><th>Price (per Gallon)</th><th>Part Number</th><th>Price per Ounce</th></tr>
      </thead>
      <tbody>
        <tr><td>1 Gallon / 1 per case</td><td>40</td><td>$37.00</td><td>CL1G</td><td>0.28906</td></tr>
        <tr><td>5 Gallon Pail</td><td>20</td><td>$25.80</td><td>CL5G</td><td>0.20156</td></tr>
        <tr><td>55 Gallon Drum</td><td>4</td><td>$20.10</td><td>CL55G</td><td>0.15703</td></tr>
        <tr><td>275 Gallon Tote</td><td>1</td><td>$20.10</td><td>CL275</td><td>0.15703</td></tr>
      </tbody>
    </table>
  </section>

  <footer class="site-footer">
    <div class="brand">Halden Supply</div>
    <p class="stock-line">In Stock Ready to Ship</p>
    <p class="call-line">Call 555-014-2290 for Inquiries</p>
    <div class="footer-actions">
      <span class="btn btn-blue">Safety Data Sheet</span>
      <span class="btn btn-dark">Spec Sheet PDF</span>
    </div>
    <div class="social"><span></span><span></span><span></span></div>
    <p class="copyright">Copyright © 2020 Clendora. All Rights Reserved.</p>
  </footer>
</body>
</html>
```